Business Card Design needed for start up company Halvora

In need of a new business card designed for a start up company based in Sydney, Halvora is a new start up innovative Company, our mission it to make property accessible for everyday Australian and to become the leading Real Estate platform in Australia. We want it to be fresh and clean.

Industry/Entity Type

Financial

Contact Information for Business Card

Section for Name
Section for Title

HALVORA - The Strength of Pooling
Mobile:
Direct:

Font styles to use
Sans Serif

Colors
33a6d7
0692cd
0255a3
ffffff

Requirements
Must have
• Logo, all business card details

```html
<!DOCTYPE html>
<html lang="en">
<head>
<meta charset="utf-8">
<title>Halvora Business Card</title>
<link href="https://fonts.googleapis.com/css2?family=Roboto:wght@400;500;700;900&family=Roboto+Condensed:wght@700&display=swap" rel="stylesheet">
<style>
  :root {
    --stage: #2b2b2d;
    --navy: #1f3f78;
    --navy-deep: #14295a;
    --sky: #33a6d7;
    --ocean: #0692cd;
    --royal: #0255a3;
    --paper: #f3f4f5;
    --ink: #3b3d42;
    --white: #ffffff;
    --divider: #9aa0a8;
  }
  * { margin: 0; padding: 0; box-sizing: border-box; }
  html, body { width: 1200px; height: 886px; overflow: hidden; }
  body {
    background: var(--stage);
    font-family: "Roboto", Arial, sans-serif;
    position: relative;
  }
  .card {
    position: absolute;
    width: 540px;
    height: 310px;
    border-radius: 18px;
    overflow: hidden;
  }
  /* Front */
  .card-front {
    left: 60px; top: 110px;
    background: var(--navy);
    display: flex;
    flex-direction: column;
    align-items: center;
    justify-content: center;
  }
  .brand {
    display: flex;
    align-items: center;
    gap: 14px;
  }
  .brand-dot {
    width: 62px; height: 62px;
    border-radius: 50%;
    background: var(--sky);
  }
  .brand-name {
    font-family: "Roboto", Arial, sans-serif;
    font-weight: 900;
    font-size: 58px;
    letter-spacing: 1px;
    color: var(--white);
    line-height: 1;
  }
  .tagline {
    margin-top: 42px;
    font-size: 15px;
    color: var(--white);
    letter-spacing: 0.3px;
  }
  /* Back */
  .card-back {
    left: 600px; top: 470px;
    background: var(--paper);
  }
  .card-bands { position: absolute; inset: 0; }
  .identity {
    position: absolute;
    right: 320px; top: 118px;
    text-align: right;
  }
  .person-name {
    font-family: "Roboto Condensed", "Arial Narrow", sans-serif;
    font-weight: 700;
    font-size: 30px;
    color: var(--navy);
    line-height: 1;
  }
  .person-title {
    margin-top: 4px;
    font-size: 15px;
    font-weight: 500;
    color: var(--ocean);
    letter-spacing: 0.4px;
  }
  .divider {
    position: absolute;
    left: 238px; top: 80px;
    width: 1px; height: 140px;
    background: var(--divider);
  }
  .contact {
    position: absolute;
    left: 256px; top: 88px;
    font-size: 14.5px;
    color: var(--ink);
    line-height: 1.2;
    list-style: none;
  }
  .contact li { display: flex; align-items: center; gap: 8px; }
  .contact .address { display: block; margin-bottom: 6px; padding-left: 18px; }
  .contact svg { width: 12px; height: 12px; flex: none; fill: var(--navy); }
</style>
</head>
<body>

<section class="card card-front" aria-label="Card front">
  <div class="brand">
    <span class="brand-dot"></span>
    <span class="brand-name">HALVORA</span>
  </div>
  <p class="tagline">The Strength of Pooling</p>
</section>

<section class="card card-back" aria-label="Card back">
  <svg class="card-bands" viewBox="0 0 540 310" width="540" height="310" aria-hidden="true">
    <path d="M0 0H540V12H262C250 12 246 28 232 28H0Z" fill="var(--sky)"/>
    <path d="M0 296H248C262 296 266 266 282 266H540V310H0Z" fill="var(--navy-deep)"/>
  </svg>

  <div class="identity">
    <h1 class="person-name">MARA ELLWOOD</h1>
    <p class="person-title">CEO/FOUNDER</p>
  </div>

  <span class="divider"></span>

  <ul class="contact">
    <li class="address">42 Harbour View Road<br>Sydney, NSW 2000</li>
    <li>
      <svg viewBox="0 0 12 12"><path d="M2.5 0.5 4.5 3 3.4 4.3Q4.8 7.2 7.7 8.6L9 7.5 11.5 9.5 10 11.5Q4.5 11 0.5 2Z"/></svg>
      02 8123 4567
    </li>
    <li>
      <svg viewBox="0 0 12 12"><path d="M3 0H9V12H3ZM4 1.5V9.5H8V1.5Z" fill-rule="evenodd"/></svg>
      0412 555 018
    </li>
    <li>
      <svg viewBox="0 0 12 12"><path d="M0 2H12V3.2L6 7 0 3.2Z"/><path d="M0 4.6 6 8.4 12 4.6V10H0Z"/></svg>
      hello@halvora.com.au
    </li>
    <li>
      <svg viewBox="0 0 12 12"><circle cx="6" cy="6" r="6"/><path d="M6 0V12M0 6H12" stroke="var(--paper)" stroke-width="1"/></svg>
      www.halvora.com.au
    </li>
  </ul>
</section>

</body>
</html>
```